Brintel Works - Fast, Efficient and Gas Mainteance for Domestic, Commercial and Industrial clients

We are in the process of purchasing a new business and would like to get a new logo and business card.
Business is a gas maintenance business that also does new gas installations.
Has been established since 1988.
Services include:
Install all types of gas appliances & equipment inc. hot water units
Maintain / repair / replace all types of gas appliances & equipment

Target Market(s)

Domestic, Commercial and Industrial clients

Industry/Entity Type

Business

Contact Information for Business Card

admin@brintelworks.com.au
07 3918 4726
Brintel Works PTY LTD

Logo Text

Gas Fitting & Plumbing Maintenance Specialists

Font styles to use
Sans Serif

Requirements
Must have
• Logo
• Business name, contact number, email address, web address
• Domestic | Commercial | Industrial Est Since 1988
Nice to have
• Possibly a black card with a flame logo to one side
Should not have
• Spelling errors

```html
<!DOCTYPE html>
<html lang="en">
<head>
<meta charset="utf-8">
<title>Brintel Works PTY LTD – Business Card</title>
<link rel="stylesheet" href="https://fonts.googleapis.com/css2?family=Open+Sans:wght@400;700;800&family=Arimo:wght@400&family=Great+Vibes&display=swap">
<style>
  :root {
    --page-bg: #dcdcdc;
    --card-bg: #ebeaea;
    --brand-red: #e2472e;
    --band-orange: #f0553a;
    --band-black: #0d0d0d;
    --band-charcoal: #2e2e2e;
    --text-dark: #3a3d44;
    --text-muted: #555a63;
    --script-grey: #7b7f86;
    --mark-grey: #cfcfcf;
    --photo-dark: #4a4f52;
    --photo-mid: #8c9095;
    --photo-fire: #e3632a;
    --white: #ffffff;
  }
  * { box-sizing: border-box; margin: 0; padding: 0; }
  html, body {
    width: 1189px;
    height: 1200px;
    overflow: hidden;
    background: var(--page-bg);
  }
  .sheet { position: relative; width: 1189px; height: 1200px; }
  .card {
    position: absolute;
    left: 140px;
    width: 917px;
    height: 523px;
    background: var(--card-bg);
    box-shadow: 0 6px 14px rgba(0,0,0,0.35);
    overflow: hidden;
  }
  .card--front { top: 46px; }
  .card--back { top: 623px; }

  .card__bands { position: absolute; inset: 0; width: 917px; height: 523px; }

  .brand-mark {
    position: absolute;
    border-radius: 50%;
    background: var(--mark-grey);
    opacity: 0.6;
  }
  .brand-name {
    position: absolute;
    font-family: "Open Sans", sans-serif;
    font-weight: 800;
    color: var(--brand-red);
    text-transform: uppercase;
    white-space: nowrap;
    letter-spacing: 0.5px;
  }
  .brand-name__suffix { font-size: 0.3em; letter-spacing: 0.5px; margin-left: 8px; }
  .tagline {
    position: absolute;
    font-family: "Open Sans", sans-serif;
    font-weight: 700;
    color: var(--text-dark);
    white-space: nowrap;
  }
  .sectors {
    position: absolute;
    font-family: "Open Sans", sans-serif;
    font-weight: 400;
    color: var(--text-muted);
    white-space: nowrap;
  }
  .sectors__est {
    font-family: "Great Vibes", cursive;
    color: var(--script-grey);
    margin-left: 14px;
  }

  /* front layout */
  .card--front .brand-mark { left: 40px; top: 80px; width: 66px; height: 66px; }
  .card--front .brand-name { left: 127px; top: 56px; font-size: 48px; }
  .card--front .tagline { left: 128px; top: 116px; font-size: 26px; }
  .card--front .sectors { left: 128px; top: 163px; font-size: 15.5px; }
  .card--front .sectors__est { font-size: 25px; }

  .contact-list {
    position: absolute;
    left: 39px;
    top: 356px;
    list-style: none;
    font-family: "Arimo", sans-serif;
    font-size: 22px;
    color: var(--white);
  }
  .contact-list__item { display: flex; align-items: center; height: 27.5px; }
  .contact-list__item + .contact-list__item { margin-top: 0.5px; }
  .contact-list__icon {
    width: 19px; height: 19px;
    background: var(--white);
    border-radius: 2px;
    margin-right: 25px;
    flex: none;
  }

  .product-visual {
    position: absolute;
    border-radius: 6px;
    background: linear-gradient(135deg, var(--photo-dark) 0%, var(--photo-dark) 45%, var(--photo-fire) 50%, var(--photo-mid) 62%, var(--photo-mid) 100%);
    opacity: 0.85;
  }
  .card--front .product-visual { left: 640px; top: 335px; width: 233px; height: 170px; }

  /* back layout */
  .card--back .brand-mark { left: 70px; top: 225px; width: 50px; height: 50px; }
  .card--back .brand-name { left: 129px; top: 206px; font-size: 40px; }
  .card--back .tagline { left: 130px; top: 255px; font-size: 23px; }
  .card--back .sectors { left: 130px; top: 296px; font-size: 13.5px; }
  .card--back .sectors__est { font-size: 22px; }
  .card--back .product-visual { left: 544px; top: 135px; width: 327px; height: 257px; }
</style>
</head>
<body>
<main class="sheet">

  <section class="card card--front" aria-label="Business card front">
    <svg class="card__bands" viewBox="0 0 917 523" aria-hidden="true">
      <path d="M0 301 Q470 300 917 116 L917 268 Q500 300 0 331 Z" fill="var(--band-charcoal)"/>
      <path d="M0 301 Q470 300 917 116 L917 196 Q480 292 0 318 Z" fill="var(--band-black)"/>
      <path d="M0 331 Q500 300 917 268 L917 523 L0 523 Z" fill="var(--band-orange)"/>
    </svg>

    <span class="brand-mark" aria-hidden="true"></span>
    <h1 class="brand-name">Brintel Works<span class="brand-name__suffix">PTY LTD</span></h1>
    <p class="tagline">Gas fitting &amp; Plumbing Specialists</p>
    <p class="sectors">Domestic | Commercial | Industrial<span class="sectors__est">Est Since 1988</span></p>

    <ul class="contact-list">
      <li class="contact-list__item">
        <svg class="contact-list__icon" viewBox="0 0 19 19" aria-label="Phone"><path d="M6 3.5 L8 6.5 L6.8 8 Q8 10.8 11 12.2 L12.5 11 L15.5 13 L14 15.5 Q8 15.5 3.5 5 Z" fill="var(--band-orange)"/></svg>
        <span>07 3918 4726</span>
      </li>
      <li class="contact-list__item">
        <svg class="contact-list__icon" viewBox="0 0 19 19" aria-label="Fax"><rect x="5.5" y="3" width="8" height="4" fill="var(--band-orange)"/><rect x="3" y="7.5" width="13" height="6" fill="var(--band-orange)"/><rect x="5.5" y="11" width="8" height="5" fill="var(--band-orange)"/></svg>
        <span>07 3918 4730</span>
      </li>
      <li class="contact-list__item">
        <svg class="contact-list__icon" viewBox="0 0 19 19" aria-label="Website"><circle cx="9.5" cy="9.5" r="6" fill="none" stroke="var(--band-orange)" stroke-width="2"/><path d="M3.5 9.5 H15.5 M9.5 3.5 V15.5" stroke="var(--band-orange)" stroke-width="1.5"/></svg>
        <span>www.brintelworks.com.au</span>
      </li>
      <li class="contact-list__item">
        <svg class="contact-list__icon" viewBox="0 0 19 19" aria-label="Email"><rect x="3" y="5" width="13" height="9" fill="none" stroke="var(--band-orange)" stroke-width="1.6"/><path d="M3 5 L9.5 10.5 L16 5" fill="none" stroke="var(--band-orange)" stroke-width="1.6"/></svg>
        <span>admin@brintelworks.com.au</span>
      </li>
      <li class="contact-list__item">
        <svg class="contact-list__icon" viewBox="0 0 19 19" aria-label="Address"><path d="M9.5 16 L5 9 A5 5 0 1 1 14 9 Z" fill="var(--band-orange)"/><circle cx="9.5" cy="7" r="1.8" fill="var(--white)"/></svg>
        <span>PO Box 2846, Coralbay Heads, QLD 4290</span>
      </li>
    </ul>

    <div class="product-visual" role="img" aria-label="Photo of a freestanding gas log heater with a visible flame beside two tall hot water units"></div>
  </section>

  <section class="card card--back" aria-label="Business card back">
    <span class="brand-mark" aria-hidden="true"></span>
    <h2 class="brand-name">Brintel Works<span class="brand-name__suffix">PTY LTD</span></h2>
    <p class="tagline">Gas fitting &amp; Plumbing Specialists</p>
    <p class="sectors">Domestic | Commercial | Industrial<span class="sectors__est">Est Since 1988</span></p>
    <div class="product-visual" role="img" aria-label="Photo of a freestanding gas log heater with a visible flame beside two tall hot water units"></div>
  </section>

</main>
</body>
</html>
```